Quillbrook Air Business Card Design

Design new, 2 sides, business cards for a residential and light commercial heating, air conditioning contractor.

Target Market(s)

Homeowners, small businesses

Industry/Entity Type

Business

Contact Information for Business Card

Dominic Westerhall
Phone - 862-415-2736
Email
Address - PO box 518
Brightwater NJ 07912
Website - www.HarborBreezeLLC.example

Requirements
Must have
• logo, company colors, standard size with no die cut, so I can use nova stamp

```html
<!DOCTYPE html>
<html lang="en">
<head>
<meta charset="utf-8">
<title>Quillbrook Air – Business Card</title>
<link href="https://fonts.googleapis.com/css2?family=Open+Sans:wght@400;600;700&display=swap" rel="stylesheet">
<style>
  :root {
    --backdrop: #6a5140;
    --card-white: #ffffff;
    --brand-maroon: #9b1f33;
    --brand-orange: #f28a30;
    --text-grey: #555555;
    --divider: #e2e2e2;
  }
  * { margin: 0; padding: 0; box-sizing: border-box; }
  html, body { width: 1200px; height: 987px; overflow: hidden; }
  body {
    background: var(--backdrop);
    font-family: "Open Sans", Arial, sans-serif;
    position: relative;
  }
  .card {
    position: absolute;
    left: 293px;
    width: 615px;
    height: 350px;
  }
  .card--front { top: 131px; background: var(--card-white); }
  .card--back { top: 506px; background: var(--brand-orange); }

  .brand-name {
    color: var(--brand-maroon);
    font-weight: 700;
    text-align: center;
    line-height: 1.05;
    text-transform: uppercase;
    white-space: nowrap;
  }
  .card--front .brand-block {
    position: absolute;
    left: 36px;
    top: 0;
    width: 260px;
    height: 100%;
    display: flex;
    align-items: center;
    justify-content: center;
    gap: 10px;
  }
  .brand-dot {
    width: 18px; height: 18px;
    border-radius: 50%;
    background: var(--brand-orange);
    flex: none;
  }
  .card--front .brand-name { font-size: 30px; }

  .divider {
    position: absolute;
    left: 320px; top: 70px;
    width: 1px; height: 235px;
    background: var(--divider);
  }
  .contact {
    position: absolute;
    left: 339px; top: 74px;
    color: var(--text-grey);
    font-size: 15px;
  }
  .contact__name {
    color: var(--brand-maroon);
    font-weight: 600;
    font-size: 21px;
    text-transform: uppercase;
    line-height: 26px;
  }
  .contact__title {
    color: var(--brand-orange);
    font-size: 16px;
    line-height: 22px;
    margin-bottom: 10px;
  }
  .contact__address { line-height: 22.5px; margin-bottom: 6px; }
  .contact__list { list-style: none; }
  .contact__list li {
    display: flex;
    align-items: center;
    gap: 7px;
    line-height: 23.5px;
  }
  .contact__list svg { width: 14px; height: 14px; fill: var(--brand-maroon); flex: none; }

  .card--back .brand-block {
    position: absolute; inset: 0;
    display: flex; align-items: center; justify-content: center;
  }
  .card--back .brand-name { font-size: 58px; }
</style>
</head>
<body>
  <section class="card card--front" aria-label="Business card front">
    <div class="brand-block">
      <span class="brand-dot"></span>
      <div class="brand-name">Quillbrook<br>Air</div>
    </div>
    <div class="divider"></div>
    <div class="contact">
      <div class="contact__name">Dominic Westerhall</div>
      <div class="contact__title">CEO/Founder</div>
      <div class="contact__address">PO box 518<br>Brightwater NJ 07912</div>
      <ul class="contact__list">
        <li><svg viewBox="0 0 16 16" aria-hidden="true"><path d="M3.6 1.2l2.3 2.6-1.3 1.9c.9 2 2.4 3.6 4.5 4.6l1.9-1.3 2.7 2.3-1.4 2.4C6.6 13.6 2.2 9.3 1.2 3.5z"/></svg>862 415 2736</li>
        <li><svg viewBox="0 0 16 16" aria-hidden="true"><path d="M4 1h8v14H4zM5.5 2.5v9h5v-9zM7.2 12.6h1.6v1.2H7.2z" fill-rule="evenodd"/></svg>862 415 2790</li>
        <li><svg viewBox="0 0 16 16" aria-hidden="true"><path d="M4 1h7v4H4zM1 6h14v6h-2v3H3v-3H1zM4.5 10v3.5h7V10z" fill-rule="evenodd"/></svg>862 415 2741</li>
        <li><svg viewBox="0 0 16 16" aria-hidden="true"><path d="M1 3.5h14v9H1z"/><path d="M2 4.5l6 4.5 6-4.5" stroke="#fff" stroke-width="1.2" fill="none"/></svg>dominic@quillbrookair.example</li>
        <li><svg viewBox="0 0 16 16" aria-hidden="true"><circle cx="8" cy="8" r="7"/><path d="M1.5 8h13M8 1.2c-2.6 3.8-2.6 9.8 0 13.6M8 1.2c2.6 3.8 2.6 9.8 0 13.6" stroke="#fff" stroke-width="1" fill="none"/></svg>www.QuillbrookAirLLC.example</li>
      </ul>
    </div>
  </section>

  <section class="card card--back" aria-label="Business card back">
    <div class="brand-block">
      <div class="brand-name">Quillbrook<br>Air</div>
    </div>
  </section>
</body>
</html>
```